UX - Need some screens design for a Skill Assessment Application

I am building an app to carry out skill assessments. Depending on how the assessment is configured, it may have one or more parts
1. Question based assessment (Multiple Choice, True False, Fill in the blanks"
2. Endorsement by two colleagues - A screen that allows user to pick colleagues based on search and shows the status of pending requests
3. A written submission - a page that explains the format of the submission and a file upload
As each assessment can be configured with or without any of the steps, the assessment UI must be such that these areas get hidden/displayed based on configuration.
Colour codes to be used can be #0e78bb and #ffffff
There will also be a start screen (instructions) and an end screen (results)
Target Market(s)
Enterprise software
Number of Pages Required
4 page

```html
<!DOCTYPE html>
<html lang="en">
<head>
<meta charset="utf-8">
<title>Skill Assessment App – Screens</title>
<link href="https://fonts.googleapis.com/css2?family=Inter:wght@400;500;600;700&display=swap" rel="stylesheet">
<style>
:root{
  --brand:#0e78bb;
  --nav:#1467b5;
  --white:#ffffff;
  --ink:#1f2a37;
  --text:#4a5562;
  --muted:#99a2ad;
  --line:#e1e5ea;
  --soft:#f3f5f7;
  --chip:#e4e7eb;
  --teal:#10939b;
  --board:#2a2a2a;
  --select:#eaf4fb;
}
*{box-sizing:border-box;margin:0;padding:0}
html,body{width:840px;height:1200px;overflow:hidden;background:var(--board)}
body{font-family:"Inter",sans-serif;color:var(--ink)}
.board{position:absolute;left:0;top:0;width:1607px;height:2296px;background:var(--board);transform:scale(0.52271);transform-origin:0 0}
.num{position:absolute;color:var(--white);font-size:40px;font-weight:700;line-height:1}
.screen{position:absolute;width:643px;height:413px;background:var(--white);overflow:hidden}
.a{position:absolute}

/* nav */
.nav{position:absolute;left:0;top:0;width:100%;height:23px;background:var(--nav)}
.brand{position:absolute;left:37px;top:6px;display:flex;align-items:center;gap:4px;color:var(--white);font-size:7px;font-weight:600}
.brand i{display:block;width:9px;height:9px;border-radius:50%;background:var(--white)}
.nav-links{position:absolute;left:261px;top:0;height:23px;display:flex;gap:11px;font-size:5.5px;color:#cfe2f3}
.nav-links span{line-height:23px;position:relative}
.nav-links .on{color:var(--white);font-weight:700}
.nav-links .on:after{content:"";position:absolute;left:0;right:0;bottom:0;height:2px;background:#8fd0ff}
.nav-icons{position:absolute;right:36px;top:5px;display:flex;gap:9px;align-items:center}
.nav-icons svg{width:8px;height:8px}
.me{display:block;width:13px;height:13px;border-radius:50%;background:linear-gradient(135deg,#c89a84,#5a3b33);border:1px solid var(--white)}

/* page head */
.crumb{position:absolute;left:30px;top:35px;display:flex;align-items:center;gap:5px;font-size:5px;color:var(--text)}
.crumb svg{width:10px;height:10px}
.crumb .link{color:var(--brand);margin-left:2px}
.page-title{position:absolute;left:47px;top:53px;display:flex;align-items:center;gap:7px}
.page-title svg{width:11px;height:11px}
.page-title h2{font-size:11.5px;font-weight:600}
.updated{position:absolute;right:48px;top:61px;font-size:5px;color:var(--text)}
.meta-band{position:absolute;left:0;top:76px;width:100%;height:22px;background:var(--soft);font-size:4.8px;color:var(--text)}
.meta-band .m{position:absolute;top:8px}
.meta-band b{font-weight:400;color:var(--brand)}
.chips{position:absolute;right:48px;top:5px;display:flex;gap:3px}
.chip{display:inline-flex;align-items:center;gap:2px;height:11px;padding:0 5px;border-radius:6px;background:var(--chip);font-size:4.8px;color:var(--text)}
.chip .ok{width:6px;height:6px}

/* steps */
.step{position:absolute;left:47px;width:115px;height:22px;border:1px solid var(--line);border-radius:2px;padding-left:9px;line-height:20px;font-size:5.5px;color:var(--muted)}
.step.active{border-color:var(--brand);color:var(--ink)}
.step.done{color:var(--text)}
.step .ok{position:absolute;right:8px;top:7px;width:7px;height:7px}

/* section */
.sect{position:absolute;left:196px;top:117px;font-size:8px;font-weight:600}
.btn-line{position:absolute;height:16px;border:1px solid var(--brand);border-radius:2px;color:var(--brand);font-size:5px;display:flex;align-items:center;justify-content:center;background:var(--white)}
.btn-fill{position:absolute;height:16px;border-radius:2px;background:var(--brand);color:var(--white);font-size:5px;display:flex;align-items:center;justify-content:center;font-weight:500}
.save{left:540px;top:115px;width:55px}
.q{position:absolute;left:196px;top:146px;font-size:6.8px;color:var(--ink)}
.q .qn{color:var(--text);margin-right:9px}
.prog{position:absolute;left:480px;top:150px;width:115px;font-size:5px;color:var(--text)}
.prog .ring{position:absolute;right:14px;top:-5px;width:15px;height:15px}
.prog .count{position:absolute;right:0;top:0;font-size:4.5px}
.note{position:absolute;left:480px;width:115px;background:var(--soft);padding:10px 11px;font-size:4.8px;line-height:1.65;color:var(--text)}
.note h4{font-size:7px;font-weight:500;color:var(--ink);margin-bottom:5px}

.opt{position:absolute;left:196px;width:251px;height:28px;border:1px solid var(--line);border-radius:2px;font-size:5px;color:var(--text);display:flex;align-items:center}
.opt .n{width:15px;height:13px;margin:0 12px 0 8px;background:#e6f1f9;color:var(--brand);display:flex;align-items:center;justify-content:center;font-size:5px}
.opt.sel{border-color:var(--brand);background:var(--select);color:var(--brand)}
.pill{position:absolute;height:15px;width:28px;border-radius:8px;border:1px solid var(--line);font-size:5px;color:var(--brand);display:flex;align-items:center;justify-content:center;background:var(--white)}
.pill.on{background:var(--brand);border-color:var(--brand);color:var(--white)}
.blank{position:absolute;border-bottom:1px solid var(--line);font-size:5.5px;color:#c5ccd3;padding-bottom:3px}
.fill-text{position:absolute;font-size:6.8px}

/* footer */
.pct{position:absolute;left:47px;top:354px;font-size:15px;font-weight:700}
.pct small{font-size:6px;font-weight:500}
.track{position:absolute;left:0;top:375px;width:100%;height:3px;background:#eef1f3}
.track i{display:block;height:3px;background:var(--teal)}
.goback{left:47px;top:387px;width:39px}
.skip{position:absolute;left:535px;top:392px;font-size:5px;color:var(--text)}
.next{left:568px;top:387px;width:27px}

/* endorsement */
.field{position:absolute;top:146px;height:16px;border:1px solid var(--line);border-radius:2px;font-size:5px;color:var(--text);padding-left:6px;line-height:14px}
.field.ph{color:var(--muted)}
.field svg{position:absolute;right:5px;top:4px;width:6px;height:6px}
.disabled{position:absolute;top:146px;left:548px;width:47px;height:16px;border:1px solid var(--line);border-radius:2px;font-size:5px;color:#c3c9cf;display:flex;align-items:center;justify-content:center}
.person{position:absolute;left:196px;width:399px;height:31px;border:1px solid var(--line);border-radius:2px}
.person .box{position:absolute;left:8px;top:11px;width:7px;height:7px;border:1px solid #d5dbe1;border-radius:1px;background:var(--white)}
.person .box.on{background:var(--brand);border-color:var(--brand)}
.person .box svg{position:absolute;left:0;top:0;width:5px;height:5px}
.avatar{position:absolute;left:21px;top:8px;width:14px;height:14px;border-radius:50%}
.person .who{position:absolute;left:41px;top:8px;font-size:5.5px;font-weight:500}
.person .who small{display:block;font-size:4.5px;font-weight:400;color:var(--muted);margin-top:2px}
.person .add{position:absolute;right:9px;top:7px;width:23px;height:15px;border:1px solid var(--brand);border-radius:2px;font-size:5px;color:var(--brand);display:flex;align-items:center;justify-content:center}
.pager{position:absolute;top:343px;font-size:5.5px;color:var(--text)}
.pager.edge{height:14px;border:1px solid var(--line);border-radius:2px;color:#c3c9cf;font-size:4.5px;display:flex;align-items:center;justify-content:center}
.pager.cur{width:15px;height:14px;background:var(--brand);color:var(--white);border-radius:2px;display:flex;align-items:center;justify-content:center}
.av1{background:linear-gradient(135deg,#b07a5a,#4a2e22)}
.av2{background:linear-gradient(135deg,#6d6d6d,#1e1e1e)}
.av3{background:linear-gradient(135deg,#c9a690,#6a4c3e)}
.av4{background:linear-gradient(135deg,#e0b27a,#a36d3f)}
.av5{background:linear-gradient(135deg,#d1a79b,#5b3a36)}

.overlay{position:absolute;left:0;top:0;width:100%;height:100%;background:rgba(30,34,40,.55)}
.modal{position:absolute;left:237px;top:132px;width:168px;height:149px;background:var(--white);border-radius:4px;padding:11px 16px}
.modal h3{font-size:7px;font-weight:600}
.modal .pair{position:absolute;left:16px;top:39px;display:flex;gap:3px}
.modal .pair span{width:12px;height:12px;border-radius:50%}
.modal p{position:absolute;left:16px;top:64px;font-size:4.6px;color:var(--text)}
.modal label{position:absolute;left:16px;top:80px;font-size:4px;color:var(--text)}
.modal .sel{position:absolute;left:15px;top:90px;width:138px;height:16px;border:1px solid var(--line);border-radius:2px;font-size:5px;padding-left:7px;line-height:14px}
.modal .sel svg{position:absolute;right:6px;top:4px;width:6px;height:6px}

/* submission */
.lbl{position:absolute;font-size:4px;color:var(--text)}
.input{position:absolute;height:16px;border:1px solid var(--line);border-radius:2px;font-size:5px;padding-left:7px;line-height:14px}
.input svg{position:absolute;right:5px;top:4px;width:6px;height:6px}
.textarea{position:absolute;left:196px;top:191px;width:251px;height:49px;border:1px solid var(--line);border-radius:2px;font-size:5px;color:var(--muted);padding:6px 7px}
.drop{position:absolute;left:196px;top:248px;width:251px;height:68px;border:1px dashed #8fc2e4;background:#eef6fc;border-radius:2px;text-align:center;font-size:5px;color:var(--text);padding-top:43px;line-height:1.5}
.drop .up{position:absolute;left:116px;top:14px;width:20px;height:20px;border-radius:50%;background:#c9e4f6}
.drop .up svg{position:absolute;left:5px;top:5px;width:10px;height:10px}
.drop b{font-weight:400;color:var(--brand)}

/* dashboard */
.hero{position:absolute;left:0;top:23px;width:100%;height:131px;background:var(--nav)}
.hero .face{position:absolute;left:30px;top:15px;width:24px;height:24px;border-radius:50%;background:linear-gradient(135deg,#c79b87,#3c2620)}
.hero .hi{position:absolute;left:65px;top:18px;font-size:5px;color:#b9d3ec}
.hero .name{position:absolute;left:65px;top:27px;font-size:8.5px;font-weight:600;color:var(--white)}
.create{position:absolute;left:517px;top:18px;width:94px;height:18px;border-radius:2px;background:#2c87d2;border:1px solid #5aa6e3;color:var(--white);font-size:5px;display:flex;align-items:center;justify-content:center;gap:4px}
.create svg{width:6px;height:6px}
.summary{position:absolute;left:30px;top:54px;font-size:5.5px;color:#d9e7f5}
.card{position:absolute;top:69px;width:139px;height:47px;border-radius:2px;background:rgba(255,255,255,.12);color:var(--white)}
.card .ic{position:absolute;left:10px;top:9px;width:13px;height:13px}
.card .big{position:absolute;left:34px;top:11px;font-size:8.5px;font-weight:600}
.card .lab{position:absolute;left:34px;top:26px;font-size:5.5px}
.card .sub{position:absolute;left:34px;top:34px;font-size:4px;color:#bcd4ec}
.list{position:absolute;left:0;top:154px;width:100%;height:259px;background:var(--soft)}
.list h3{position:absolute;left:38px;top:12px;font-size:8px;font-weight:600}
.tabs{position:absolute;left:38px;top:34px;display:flex;font-size:5px}
.tabs span{height:16px;line-height:16px;padding:0 9px;background:#e2e6ea;color:var(--text)}
.tabs .on{background:var(--brand);color:var(--white)}
.views{position:absolute;right:36px;top:37px;display:flex;gap:8px}
.views svg{width:9px;height:9px}
.thead{position:absolute;left:38px;top:58px;width:567px;height:18px;background:#e6e9ed;font-size:4.2px;color:var(--text)}
.thead span,.row span{position:absolute}
.thead span{top:7px}
.row{position:absolute;left:38px;width:567px;height:27px;background:var(--white);font-size:5px;color:var(--text)}
.row span{top:11px}
.row .t{color:var(--brand)}
.row .cs{position:absolute;left:365px;top:8px;display:flex;gap:4px}
.row .kebab{position:absolute;left:543px;top:9px;width:3px;height:9px}
</style>
</head>
<body>
<div class="board">

  <div class="num" style="left:424px;top:55px">1</div>
  <div class="num" style="left:78px;top:514px">2</div>
  <div class="num" style="left:838px;top:514px">3</div>
  <div class="num" style="left:78px;top:950px">4</div>
  <div class="num" style="left:838px;top:950px">5</div>
  <div class="num" style="left:78px;top:1386px">6</div>
  <div class="num" style="left:838px;top:1386px">7</div>
  <div class="num" style="left:78px;top:1822px">8</div>
  <div class="num" style="left:838px;top:1822px">9</div>

  <!-- Dashboard -->
  <section class="screen" style="left:474px;top:57px;width:642px">
    <div class="nav">
      <div class="brand"><i></i>Skillmark</div>
      <div class="nav-links"><span class="on">Assessments</span><span>Colleagues</span><span>Results</span></div>
      <div class="nav-icons">
        <svg viewBox="0 0 16 16" fill="none" stroke="#fff" stroke-width="1.4"><path d="M4 11V7a4 4 0 0 1 8 0v4l1 1H3z"/><path d="M7 14h2"/></svg>
        <svg viewBox="0 0 16 16" fill="none" stroke="#fff" stroke-width="1.4"><circle cx="8" cy="8" r="2.3"/><circle cx="8" cy="8" r="5.5" stroke-dasharray="2.2 1.4"/></svg>
        <span class="me" role="img" aria-label="User profile photo"></span>
      </div>
    </div>
    <div class="hero">
      <span class="face" role="img" aria-label="User profile photo"></span>
      <div class="hi">Welcome back!</div>
      <div class="name">Rania T. Wirawan</div>
      <div class="create"><svg viewBox="0 0 12 12" fill="none" stroke="#fff" stroke-width="1.2"><rect x="2" y="1.5" width="8" height="9" rx="1"/><path d="M6 4v4M4 6h4"/></svg>Create New Assessment</div>
      <div class="summary">Summary</div>
      <div class="card" style="left:31px">
        <svg class="ic" viewBox="0 0 16 16" fill="none" stroke="#fff" stroke-width="1.2"><rect x="2.5" y="1.5" width="10" height="13" rx="1"/><path d="M5 5h5M5 8h3"/><circle cx="10" cy="11" r="2"/></svg>
        <div class="big">7</div><div class="lab">My Assessments</div><div class="sub">3 pending</div>
      </div>
      <div class="card" style="left:178px">
        <svg class="ic" viewBox="0 0 16 16" fill="none" stroke="#fff" stroke-width="1.2"><path d="M2 14h12M4 14V9h8v5"/><circle cx="8" cy="4.5" r="2"/></svg>
        <div class="big">3</div><div class="lab">Endorsements</div><div class="sub">1 pending</div>
      </div>
      <div class="card" style="left:325px">
        <svg class="ic" viewBox="0 0 16 16" fill="none" stroke="#fff" stroke-width="1.2"><circle cx="5" cy="5" r="2"/><circle cx="11" cy="5" r="2"/><path d="M1.5 13c.5-3 6.5-3 7 0M7.5 13c.5-3 6.5-3 7 0"/></svg>
        <div class="big">10</div><div class="lab">Colleagues</div><div class="sub">Last updated on May 23, 2024</div>
      </div>
      <div class="card" style="left:472px">
        <svg class="ic" viewBox="0 0 16 16" fill="none" stroke="#fff" stroke-width="1.2"><path d="M2 9v4h12V9M8 10V2M5 5l3-3 3 3"/></svg>
        <div class="big">7</div><div class="lab">Submissions</div><div class="sub">Last submit on May 23, 2024</div>
      </div>
    </div>
    <div class="list">
      <h3>Assessments</h3>
      <div class="tabs"><span class="on">Pending 3</span><span>Completed 4</span></div>
      <div class="views">
        <svg viewBox="0 0 12 12" fill="none" stroke="#8a94a0" stroke-width="1"><path d="M2 3h8M2 6h8M2 9h8"/></svg>
        <svg viewBox="0 0 12 12" fill="none" stroke="#0e78bb" stroke-width="1"><rect x="1.5" y="1.5" width="3.5" height="3.5"/><rect x="7" y="1.5" width="3.5" height="3.5"/><rect x="1.5" y="7" width="3.5" height="3.5"/><rect x="7" y="7" width="3.5" height="3.5"/></svg>
      </div>
      <div class="thead">
        <span style="left:9px">ASSESSMENT ID</span><span style="left:77px">ASSESSMENT TITLE</span>
        <span style="left:238px">PUBLISHED ON</span><span style="left:305px">DUE DATE</span><span style="left:530px">ACTIONS</span>
      </div>
      <div class="row" style="top:81px">
        <span style="left:9px">1723091983</span><span class="t" style="left:77px">Application Design Capabilities</span>
        <span style="left:238px">20/05/2024</span><span style="left:305px">24/05/2024</span>
        <div class="cs"><span class="chip">Quiz</span><span class="chip">Endorsement</span><span class="chip">Submission</span></div>
        <svg class="kebab" viewBox="0 0 3 9" fill="#4a5562"><circle cx="1.5" cy="1.5" r=".8"/><circle cx="1.5" cy="4.5" r=".8"/><circle cx="1.5" cy="7.5" r=".8"/></svg>
      </div>
      <div class="row" style="top:114px">
        <span style="left:9px">2317091983</span><span class="t" style="left:77px">UI/UX Designer</span>
        <span style="left:238px">20/05/2024</span><span style="left:305px">24/05/2024</span>
        <div class="cs"><span class="chip">Quiz <svg class="ok" viewBox="0 0 8 8"><circle cx="4" cy="4" r="4" fill="#10939b"/><path d="M2.3 4.1l1.2 1.2 2.3-2.5" stroke="#fff" fill="none" stroke-width=".9"/></svg></span><span class="chip">Endorsement</span></div>
        <svg class="kebab" viewBox="0 0 3 9" fill="#4a5562"><circle cx="1.5" cy="1.5" r=".8"/><circle cx="1.5" cy="4.5" r=".8"/><circle cx="1.5" cy="7.5" r=".8"/></svg>
      </div>
      <div class="row" style="top:147px">
        <span style="left:9px">1983172309</span><span class="t" style="left:77px">Sales Representative</span>
        <span style="left:238px">20/05/2024</span><span style="left:305px">24/05/2024</span>
        <div class="cs"><span class="chip">Quiz <svg class="ok" viewBox="0 0 8 8"><circle cx="4" cy="4" r="4" fill="#10939b"/><path d="M2.3 4.1l1.2 1.2 2.3-2.5" stroke="#fff" fill="none" stroke-width=".9"/></svg></span><span class="chip">Endorsement <svg class="ok" viewBox="0 0 8 8"><circle cx="4" cy="4" r="4" fill="#10939b"/><path d="M2.3 4.1l1.2 1.2 2.3-2.5" stroke="#fff" fill="none" stroke-width=".9"/></svg></span><span class="chip">Submission</span></div>
        <svg class="kebab" viewBox="0 0 3 9" fill="#4a5562"><circle cx="1.5" cy="1.5" r=".8"/><circle cx="1.5" cy="4.5" r=".8"/><circle cx="1.5" cy="7.5" r=".8"/></svg>
      </div>
    </div>
  </section>

  <!-- 2: Multiple choice -->
  <section class="screen" style="left:121px;top:517px">
    <div class="nav"><div class="brand"><i></i>Skillmark</div><div class="nav-links"><span class="on">Assessments</span><span>Colleagues</span><span>Results</span></div><div class="nav-icons"><svg viewBox="0 0 16 16" fill="none" stroke="#fff" stroke-width="1.4"><path d="M4 11V7a4 4 0 0 1 8 0v4l1 1H3z"/><path d="M7 14h2"/></svg><svg viewBox="0 0 16 16" fill="none" stroke="#fff" stroke-width="1.4"><circle cx="8" cy="8" r="2.3"/><circle cx="8" cy="8" r="5.5" stroke-dasharray="2.2 1.4"/></svg><span class="me" role="img" aria-label="User profile photo"></span></div></div>
    <div class="crumb"><svg viewBox="0 0 12 12" fill="none" stroke="#0e78bb" stroke-width="1"><circle cx="6" cy="6" r="5"/><path d="M8.5 6h-5M5.5 4L3.5 6l2 2"/></svg><span class="link">Assessment</span>/<span>Application Design Capabilities</span></div>
    <div class="page-title"><svg viewBox="0 0 12 12" fill="none" stroke="#1f2a37" stroke-width="1"><rect x="1.5" y="1" width="8" height="10" rx=".8"/><path d="M3.5 4h4M3.5 6h2.5"/><circle cx="8" cy="8.5" r="1.8"/></svg><h2>Application Design Capabilities</h2></div>
    <div class="updated">Last Updated: 23/05/2024</div>
    <div class="meta-band"><span class="m" style="left:47px">Assessment Date: <b>May 20, 2024</b></span><span class="m" style="left:154px">Assessment Type: <b>UI/UX Skill</b></span><span class="m" style="left:253px">Due Date: 24/05/2024</span><div class="chips"><span class="chip">Quiz</span><span class="chip">Endorsement</span><span class="chip">Submission</span></div></div>
    <div class="step active" style="top:117px">Quiz</div><div class="step" style="top:145px">Endorsement</div><div class="step" style="top:172px">Submission</div>
    <div class="sect">Quiz</div><div class="btn-line save">Save Progress</div>
    <div class="q"><span class="qn">Q.5.</span>What's your knowledge regarding User Interface?</div>
    <div class="prog">›&nbsp; Progress<svg class="ring" viewBox="0 0 16 16"><circle cx="8" cy="8" r="6.5" fill="none" stroke="#e1e5ea" stroke-width="1.5"/><circle cx="8" cy="8" r="6.5" fill="none" stroke="#0e78bb" stroke-width="1.5" stroke-dasharray="25.5 40.8" transform="rotate(-90 8 8)"/></svg><span class="count">5 / 8</span></div>
    <div class="opt" style="top:170px"><span class="n">1</span>Lorem ipsum dolor sit amet, consecteteur adispiscing elit.</div>
    <div class="opt" style="top:203px"><span class="n">2</span>Lorem ipsum dolor sit amet, consecteteur adispiscing elit.</div>
    <div class="opt sel" style="top:236px"><span class="n">3</span>Lorem ipsum dolor sit amet, consecteteur adispiscing elit.</div>
    <div class="opt" style="top:269px"><span class="n">4</span>Lorem ipsum dolor sit amet, consecteteur adispiscing elit.</div>
    <div class="note" style="top:174px;height:112px"><h4>Note</h4>Lorem ipsum dolor sit amet, consecteteur adispiscing elit. Lorem ipsum dolor sit amet, consecteteur adispiscing elit.Lorem ipsum dolor sit amet, consecteteur adispiscing elit.</div>
    <div class="pct">20<small>%</small></div><div class="track"><i style="width:149px"></i></div>
    <div class="btn-line goback">Go Back</div><div class="skip">Skip ›</div><div class="btn-fill next">Next</div>
  </section>

  <!-- 3: Single true/false -->
  <section class="screen" style="left:885px;top:517px">
    <div class="nav"><div class="brand"><i></i>Skillmark</div><div class="nav-links"><span class="on">Assessments</span><span>Colleagues</span><span>Results</span></div><div class="nav-icons"><svg viewBox="0 0 16 16" fill="none" stroke="#fff" stroke-width="1.4"><path d="M4 11V7a4 4 0 0 1 8 0v4l1 1H3z"/><path d="M7 14h2"/></svg><svg viewBox="0 0 16 16" fill="none" stroke="#fff" stroke-width="1.4"><circle cx="8" cy="8" r="2.3"/><circle cx="8" cy="8" r="5.5" stroke-dasharray="2.2 1.4"/></svg><span class="me" role="img" aria-label="User profile photo"></span></div></div>
    <div class="crumb"><svg viewBox="0 0 12 12" fill="none" stroke="#0e78bb" stroke-width="1"><circle cx="6" cy="6" r="5"/><path d="M8.5 6h-5M5.5 4L3.5 6l2 2"/></svg><span class="link">Assessment</span>/<span>Application Design Capabilities</span></div>
    <div class="page-title"><svg viewBox="0 0 12 12" fill="none" stroke="#1f2a37" stroke-width="1"><rect x="1.5" y="1" width="8" height="10" rx=".8"/><path d="M3.5 4h4M3.5 6h2.5"/><circle cx="8" cy="8.5" r="1.8"/></svg><h2>Application Design Capabilities</h2></div>
    <div class="updated">Last Updated: 23/05/2024</div>
    <div class="meta-band"><span class="m" style="left:47px">Assessment Date: <b>May 20, 2024</b></span><span class="m" style="left:154px">Assessment Type: <b>UI/UX Skill</b></span><span class="m" style="left:253px">Due Date: 24/05/2024</span><div class="chips"><span class="chip">Quiz</span><span class="chip">Endorsement</span><span class="chip">Submission</span></div></div>
    <div class="step active" style="top:117px">Quiz</div><div class="step" style="top:145px">Endorsement</div><div class="step" style="top:172px">Submission</div>
    <div class="sect">Quiz</div><div class="btn-line save">Save Progress</div>
    <div class="q"><span class="qn">Q.7.</span>This is a single question with T/F choice</div>
    <div class="prog">›&nbsp; Progress<svg class="ring" viewBox="0 0 16 16"><circle cx="8" cy="8" r="6.5" fill="none" stroke="#e1e5ea" stroke-width="1.5"/><circle cx="8" cy="8" r="6.5" fill="none" stroke="#0e78bb" stroke-width="1.5" stroke-dasharray="35.7 40.8" transform="rotate(-90 8 8)"/></svg><span class="count">7 / 8</span></div>
    <div class="pill on" style="left:222px;top:170px">True</div><div class="pill" style="left:254px;top:170px">False</div>
    <div class="note" style="top:174px;height:69px"><h4>Note</h4>Lorem ipsum dolor sit amet, consecteteur adispiscing elit. Lorem ipsum dolor sit amet</div>
    <div class="pct">35<small>%</small></div><div class="track"><i style="width:249px"></i></div>
    <div class="btn-line goback">Go Back</div><div class="skip">Skip ›</div><div class="btn-fill next">Next</div>
  </section>

  <!-- 4: Multiple true/false -->
  <section class="screen" style="left:121px;top:953px">
    <div class="nav"><div class="brand"><i></i>Skillmark</div><div class="nav-links"><span class="on">Assessments</span><span>Colleagues</span><span>Results</span></div><div class="nav-icons"><svg viewBox="0 0 16 16" fill="none" stroke="#fff" stroke-width="1.4"><path d="M4 11V7a4 4 0 0 1 8 0v4l1 1H3z"/><path d="M7 14h2"/></svg><svg viewBox="0 0 16 16" fill="none" stroke="#fff" stroke-width="1.4"><circle cx="8" cy="8" r="2.3"/><circle cx="8" cy="8" r="5.5" stroke-dasharray="2.2 1.4"/></svg><span class="me" role="img" aria-label="User profile photo"></span></div></div>
    <div class="crumb"><svg viewBox="0 0 12 12" fill="none" stroke="#0e78bb" stroke-width="1"><circle cx="6" cy="6" r="5"/><path d="M8.5 6h-5M5.5 4L3.5 6l2 2"/></svg><span class="link">Assessment</span>/<span>Application Design Capabilities</span></div>
    <div class="page-title"><svg viewBox="0 0 12 12" fill="none" stroke="#1f2a37" stroke-width="1"><rect x="1.5" y="1" width="8" height="10" rx=".8"/><path d="M3.5 4h4M3.5 6h2.5"/><circle cx="8" cy="8.5" r="1.8"/></svg><h2>Application Design Capabilities</h2></div>
    <div class="updated">Last Updated: 23/05/2024</div>
    <div class="meta-band"><span class="m" style="left:47px">Assessment Date: <b>May 20, 2024</b></span><span class="m" style="left:154px">Assessment Type: <b>UI/UX Skill</b></span><span class="m" style="left:253px">Due Date: 24/05/2024</span><div class="chips"><span class="chip">Quiz</span><span class="chip">Endorsement</span><span class="chip">Submission</span></div></div>
    <div class="step active" style="top:117px">Quiz</div><div class="step" style="top:145px">Endorsement</div><div class="step" style="top:172px">Submission</div>
    <div class="sect">Quiz</div><div class="btn-line save">Save Progress</div>
    <div class="q"><span class="qn">Q.6.</span>This is multiple question with T/F choice</div>
    <div class="prog">›&nbsp; Progress<svg class="ring" viewBox="0 0 16 16"><circle cx="8" cy="8" r="6.5" fill="none" stroke="#e1e5ea" stroke-width="1.5"/><circle cx="8" cy="8" r="6.5" fill="none" stroke="#0e78bb" stroke-width="1.5" stroke-dasharray="30.6 40.8" transform="rotate(-90 8 8)"/></svg><span class="count">6 / 8</span></div>
    <div class="opt" style="top:170px;height:30px"><span class="n">1</span>Lorem ipsum dolor sit amet?</div>
    <div class="pill on" style="left:383px;top:177px">True</div><div class="pill" style="left:414px;top:177px">False</div>
    <div class="opt" style="top:205px;height:30px"><span class="n">2</span>Lorem ipsum dolor sit amet?</div>
    <div class="pill" style="left:383px;top:212px">True</div><div class="pill on" style="left:414px;top:212px">False</div>
    <div class="opt" style="top:240px;height:30px"><span class="n">3</span>Lorem ipsum dolor sit amet?</div>
    <div class="pill on" style="left:383px;top:247px">True</div><div class="pill" style="left:414px;top:247px">False</div>
    <div class="note" style="top:174px;height:65px"><h4>Note</h4>Lorem ipsum dolor sit amet, consecteteur adispiscing elit. Lorem ipsum dolor sit amet</div>
    <div class="pct">27<small>%</small></div><div class="track"><i style="width:184px"></i></div>
    <div class="btn-line goback">Go Back</div><div class="skip">Skip ›</div><div class="btn-fill next">Next</div>
  </section>

  <!-- 5: Fill in the blanks -->
  <section class="screen" style="left:885px;top:953px">
    <div class="nav"><div class="brand"><i></i>Skillmark</div><div class="nav-links"><span class="on">Assessments</span><span>Colleagues</span><span>Results</span></div><div class="nav-icons"><svg viewBox="0 0 16 16" fill="none" stroke="#fff" stroke-width="1.4"><path d="M4 11V7a4 4 0 0 1 8 0v4l1 1H3z"/><path d="M7 14h2"/></svg><svg viewBox="0 0 16 16" fill="none" stroke="#fff" stroke-width="1.4"><circle cx="8" cy="8" r="2.3"/><circle cx="8" cy="8" r="5.5" stroke-dasharray="2.2 1.4"/></svg><span class="me" role="img" aria-label="User profile photo"></span></div></div>
    <div class="crumb"><svg viewBox="0 0 12 12" fill="none" stroke="#0e78bb" stroke-width="1"><circle cx="6" cy="6" r="5"/><path d="M8.5 6h-5M5.5 4L3.5 6l2 2"/></svg><span class="link">Assessment</span>/<span>Application Design Capabilities</span></div>
    <div class="page-title"><svg viewBox="0 0 12 12" fill="none" stroke="#1f2a37" stroke-width="1"><rect x="1.5" y="1" width="8" height="10" rx=".8"/><path d="M3.5 4h4M3.5 6h2.5"/><circle cx="8" cy="8.5" r="1.8"/></svg><h2>Application Design Capabilities</h2></div>
    <div class="updated">Last Updated: 23/05/2024</div>
    <div class="meta-band"><span class="m" style="left:47px">Assessment Date: <b>May 20, 2024</b></span><span class="m" style="left:154px">Assessment Type: <b>UI/UX Skill</b></span><span class="m" style="left:253px">Due Date: 24/05/2024</span><div class="chips"><span class="chip">Quiz</span><span class="chip">Endorsement</span><span class="chip">Submission</span></div></div>
    <div class="step active" style="top:117px">Quiz</div><div class="step" style="top:145px">Endorsement</div><div class="step" style="top:172px">Submission</div>
    <div class="sect">Quiz</div><div class="btn-line save">Save Progress</div>
    <div class="q"><span class="qn">Q.8.</span>How do you</div>
    <div class="blank" style="left:275px;top:146px;width:82px">Type a label</div>
    <div class="fill-text" style="left:364px;top:146px">in</div>
    <div class="blank" style="left:377px;top:146px;width:82px">Type a label</div>
    <div class="fill-text" style="left:222px;top:171px">This is a fill in the</div>
    <div class="blank" style="left:296px;top:171px;width:82px">blanks</div>
    <div class="fill-text" style="left:388px;top:171px">field. Please</div>
    <div class="fill-text" style="left:222px;top:196px">sign your name:</div>
    <div class="blank" style="left:296px;top:196px;width:87px">here</div>
    <div class="fill-text" style="left:388px;top:196px">. Thank you</div>
    <div class="prog">›&nbsp; Progress<svg class="ring" viewBox="0 0 16 16"><circle cx="8" cy="8" r="6.5" fill="none" stroke="#e1e5ea" stroke-width="1.5"/><circle cx="8" cy="8" r="6.5" fill="none" stroke="#0e78bb" stroke-width="1.5" stroke-dasharray="40.8 40.8" transform="rotate(-90 8 8)"/></svg><span class="count">8 / 8</span></div>
    <div class="note" style="top:174px;height:80px"><h4>Note</h4>Lorem ipsum dolor sit amet, consecteteur adispiscing elit. Lorem ipsum dolor sit amet, consecteteur adispiscing.</div>
    <div class="pct">50<small>%</small></div><div class="track"><i style="width:321px"></i></div>
    <div class="btn-line goback">Go Back</div><div class="skip">Skip ›</div><div class="btn-fill next">Next</div>
  </section>

  <!-- 6: Endorsement -->
  <section class="screen" style="left:121px;top:1389px">
    <div class="nav"><div class="brand"><i></i>Skillmark</div><div class="nav-links"><span class="on">Assessments</span><span>Colleagues</span><span>Results</span></div><div class="nav-icons"><svg viewBox="0 0 16 16" fill="none" stroke="#fff" stroke-width="1.4"><path d="M4 11V7a4 4 0 0 1 8 0v4l1 1H3z"/><path d="M7 14h2"/></svg><svg viewBox="0 0 16 16" fill="none" stroke="#fff" stroke-width="1.4"><circle cx="8" cy="8" r="2.3"/><circle cx="8" cy="8" r="5.5" stroke-dasharray="2.2 1.4"/></svg><span class="me" role="img" aria-label="User profile photo"></span></div></div>
    <div class="crumb"><svg viewBox="0 0 12 12" fill="none" stroke="#0e78bb" stroke-width="1"><circle cx="6" cy="6" r="5"/><path d="M8.5 6h-5M5.5 4L3.5 6l2 2"/></svg><span class="link">Assessment</span>/<span>Application Design Capabilities</span></div>
    <div class="page-title"><svg viewBox="0 0 12 12" fill="none" stroke="#1f2a37" stroke-width="1"><rect x="1.5" y="1" width="8" height="10" rx=".8"/><path d="M3.5 4h4M3.5 6h2.5"/><circle cx="8" cy="8.5" r="1.8"/></svg><h2>Application Design Capabilities</h2></div>
    <div class="updated">Last Updated: 23/05/2024</div>
    <div class="meta-band"><span class="m" style="left:47px">Assessment Date: <b>May 20, 2024</b></span><span class="m" style="left:154px">Assessment Type: <b>UI/UX Skill</b></span><span class="m" style="left:253px">Due Date: 24/05/2024</span><div class="chips"><span class="chip">Quiz</span><span class="chip">Endorsement</span><span class="chip">Submission</span></div></div>
    <div class="step done" style="top:117px">Quiz<svg class="ok" viewBox="0 0 8 8"><circle cx="4" cy="4" r="4" fill="#10939b"/><path d="M2.3 4.1l1.2 1.2 2.3-2.5" stroke="#fff" fill="none" stroke-width=".9"/></svg></div><div class="step active" style="top:145px">Endorsement</div><div class="step" style="top:172px">Submission</div>
    <div class="sect">Endorsement</div><div class="btn-line save">Save Progress</div>
    <div class="field" style="left:196px;width:152px">All categories<svg viewBox="0 0 8 8" fill="none" stroke="#4a5562" stroke-width="1"><path d="M2 3l2 2 2-2"/></svg></div>
    <div class="field ph" style="left:352px;width:126px">Search<svg viewBox="0 0 8 8" fill="none" stroke="#4a5562" stroke-width="1"><circle cx="3.5" cy="3.5" r="2.5"/><path d="M5.5 5.5L7.5 7.5"/></svg></div>
    <div class="btn-fill" style="left:485px;top:146px;width:34px">Search</div>
    <div class="disabled">Send Request</div>
    <div class="person" style="top:168px"><span class="box"></span><span class="avatar av1" role="img" aria-label="Colleague photo"></span><div class="who">Mei Lin Tan<small>Application Design Capabilities</small></div><span class="add">Add</span></div>
    <div class="person" style="top:201px"><span class="box"></span><span class="avatar av2" role="img" aria-label="Colleague photo"></span><div class="who">Harold Dunmore<small>UI/UX Designer</small></div><span class="add">Add</span></div>
    <div class="person" style="top:235px"><span class="box"></span><span class="avatar av3" role="img" aria-label="Colleague photo"></span><div class="who">Mark Tolliver<small>Front-end Developer</small></div><span class="add">Add</span></div>
    <div class="person" style="top:268px"><span class="box"></span><span class="avatar av4" role="img" aria-label="Colleague photo"></span><div class="who">Alina Kessler<small>Cybersecurity Analyst</small></div><span class="add">Add</span></div>
    <div class="person" style="top:302px"><span class="box"></span><span class="avatar av5" role="img" aria-label="Colleague photo"></span><div class="who">Rupert Calder<small>DevOps Engineer</small></div><span class="add">Add</span></div>
    <div class="pager edge" style="left:423px;width:32px">‹ Back</div><div class="pager cur" style="left:463px">1</div>
    <div class="pager" style="left:488px;top:346px">2</div><div class="pager" style="left:506px;top:346px">3</div><div class="pager" style="left:524px;top:346px">4</div><div class="pager" style="left:543px;top:346px">5</div>
    <div class="pager edge" style="left:567px;width:28px">Next ›</div>
    <div class="pct">65<small>%</small></div><div class="track"><i style="width:402px"></i></div>
    <div class="btn-line goback">Go Back</div><div class="skip">Skip ›</div><div class="btn-fill next">Next</div>
  </section>

  <!-- 7: Endorsement selected -->
  <section class="screen" style="left:885px;top:1389px">
    <div class="nav"><div class="brand"><i></i>Skillmark</div><div class="nav-links"><span class="on">Assessments</span><span>Colleagues</span><span>Results</span></div><div class="nav-icons"><svg viewBox="0 0 16 16" fill="none" stroke="#fff" stroke-width="1.4"><path d="M4 11V7a4 4 0 0 1 8 0v4l1 1H3z"/><path d="M7 14h2"/></svg><svg viewBox="0 0 16 16" fill="none" stroke="#fff" stroke-width="1.4"><circle cx="8" cy="8" r="2.3"/><circle cx="8" cy="8" r="5.5" stroke-dasharray="2.2 1.4"/></svg><span class="me" role="img" aria-label="User profile photo"></span></div></div>
    <div class="crumb"><svg viewBox="0 0 12 12" fill="none" stroke="#0e78bb" stroke-width="1"><circle cx="6" cy="6" r="5"/><path d="M8.5 6h-5M5.5 4L3.5 6l2 2"/></svg><span class="link">Assessment</span>/<span>Application Design Capabilities</span></div>
    <div class="page-title"><svg viewBox="0 0 12 12" fill="none" stroke="#1f2a37" stroke-width="1"><rect x="1.5" y="1" width="8" height="10" rx=".8"/><path d="M3.5 4h4M3.5 6h2.5"/><circle cx="8" cy="8.5" r="1.8"/></svg><h2>Application Design Capabilities</h2></div>
    <div class="updated">Last Updated: 23/05/2024</div>
    <div class="meta-band"><span class="m" style="left:47px">Assessment Date: <b>May 20, 2024</b></span><span class="m" style="left:154px">Assessment Type: <b>UI/UX Skill</b></span><span class="m" style="left:253px">Due Date: 24/05/2024</span><div class="chips"><span class="chip">Quiz</span><span class="chip">Endorsement</span><span class="chip">Submission</span></div></div>
    <div class="step done" style="top:117px">Quiz<svg class="ok" viewBox="0 0 8 8"><circle cx="4" cy="4" r="4" fill="#10939b"/><path d="M2.3 4.1l1.2 1.2 2.3-2.5" stroke="#fff" fill="none" stroke-width=".9"/></svg></div><div class="step active" style="top:145px">Endorsement</div><div class="step" style="top:172px">Submission</div>
    <div class="sect">Endorsement</div><div class="btn-line save">Save Progress</div>
    <div class="field" style="left:196px;width:152px">All categories<svg viewBox="0 0 8 8" fill="none" stroke="#4a5562" stroke-width="1"><path d="M2 3l2 2 2-2"/></svg></div>
    <div class="field ph" style="left:352px;width:126px">Search<svg viewBox="0 0 8 8" fill="none" stroke="#4a5562" stroke-width="1"><circle cx="3.5" cy="3.5" r="2.5"/><path d="M5.5 5.5L7.5 7.5"/></svg></div>
    <div class="btn-fill" style="left:485px;top:146px;width:34px">Search</div>
    <div class="disabled">Send Request</div>
    <div class="person" style="top:168px"><span class="box"></span><span class="avatar av1" role="img" aria-label="Colleague photo"></span><div class="who">Mei Lin Tan<small>Application Design Capabilities</small></div><span class="add">Add</span></div>
    <div class="person" style="top:201px"><span class="box"></span><span class="avatar av2" role="img" aria-label="Colleague photo"></span><div class="who">Harold Dunmore<small>UI/UX Designer</small></div><span class="add">Add</span></div>
    <div class="person" style="top:235px"><span class="box on"><svg viewBox="0 0 5 5" fill="none" stroke="#fff" stroke-width=".8"><path d="M1 2.6l1 1 2-2.2"/></svg></span><span class="avatar av3" role="img" aria-label="Colleague photo"></span><div class="who">Mark Tolliver<small>Front-end Developer</small></div><span class="add">Add</span></div>
    <div class="person" style="top:268px"><span class="box"></span><span class="avatar av4" role="img" aria-label="Colleague photo"></span><div class="who">Alina Kessler<small>Cybersecurity Analyst</small></div><span class="add">Add</span></div>
    <div class="person" style="top:302px"><span class="box on"><svg viewBox="0 0 5 5" fill="none" stroke="#fff" stroke-width=".8"><path d="M1 2.6l1 1 2-2.2"/></svg></span><span class="avatar av5" role="img" aria-label="Colleague photo"></span><div class="who">Rupert Calder<small>DevOps Engineer</small></div><span class="add">Add</span></div>
    <div class="pager edge" style="left:423px;width:32px">‹ Back</div><div class="pager cur" style="left:463px">1</div>
    <div class="pager" style="left:488px;top:346px">2</div><div class="pager" style="left:506px;top:346px">3</div><div class="pager" style="left:524px;top:346px">4</div><div class="pager" style="left:543px;top:346px">5</div>
    <div class="pager edge" style="left:567px;width:28px">Next ›</div>
    <div class="pct">65<small>%</small></div><div class="track"><i style="width:402px"></i></div>
    <div class="btn-line goback">Go Back</div><div class="skip">Skip ›</div><div class="btn-fill next">Next</div>
  </section>

  <!-- 8: Endorsement confirm -->
  <section class="screen" style="left:121px;top:1825px">
    <div class="nav"><div class="brand"><i></i>Skillmark</div><div class="nav-links"><span class="on">Assessments</span><span>Colleagues</span><span>Results</span></div><div class="nav-icons"><svg viewBox="0 0 16 16" fill="none" stroke="#fff" stroke-width="1.4"><path d="M4 11V7a4 4 0 0 1 8 0v4l1 1H3z"/><path d="M7 14h2"/></svg><svg viewBox="0 0 16 16" fill="none" stroke="#fff" stroke-width="1.4"><circle cx="8" cy="8" r="2.3"/><circle cx="8" cy="8" r="5.5" stroke-dasharray="2.2 1.4"/></svg><span class="me" role="img" aria-label="User profile photo"></span></div></div>
    <div class="crumb"><svg viewBox="0 0 12 12" fill="none" stroke="#0e78bb" stroke-width="1"><circle cx="6" cy="6" r="5"/><path d="M8.5 6h-5M5.5 4L3.5 6l2 2"/></svg><span class="link">Assessment</span>/<span>Application Design Capabilities</span></div>
    <div class="page-title"><svg viewBox="0 0 12 12" fill="none" stroke="#1f2a37" stroke-width="1"><rect x="1.5" y="1" width="8" height="10" rx=".8"/><path d="M3.5 4h4M3.5 6h2.5"/><circle cx="8" cy="8.5" r="1.8"/></svg><h2>Application Design Capabilities</h2></div>
    <div class="updated">Last Updated: 23/05/2024</div>
    <div class="meta-band"><span class="m" style="left:47px">Assessment Date: <b>May 20, 2024</b></span><span class="m" style="left:154px">Assessment Type: <b>UI/UX Skill</b></span><span class="m" style="left:253px">Due Date: 24/05/2024</span><div class="chips"><span class="chip">Quiz</span><span class="chip">Endorsement</span><span class="chip">Submission</span></div></div>
    <div class="step done" style="top:117px">Quiz<svg class="ok" viewBox="0 0 8 8"><circle cx="4" cy="4" r="4" fill="#10939b"/><path d="M2.3 4.1l1.2 1.2 2.3-2.5" stroke="#fff" fill="none" stroke-width=".9"/></svg></div><div class="step active" style="top:145px">Endorsement</div><div class="step" style="top:172px">Submission</div>
    <div class="sect">Endorsement</div><div class="btn-line save">Save Progress</div>
    <div class="field" style="left:196px;width:152px">All categories<svg viewBox="0 0 8 8" fill="none" stroke="#4a5562" stroke-width="1"><path d="M2 3l2 2 2-2"/></svg></div>
    <div class="field ph" style="left:352px;width:126px">Search<svg viewBox="0 0 8 8" fill="none" stroke="#4a5562" stroke-width="1"><circle cx="3.5" cy="3.5" r="2.5"/><path d="M5.5 5.5L7.5 7.5"/></svg></div>
    <div class="btn-fill" style="left:485px;top:146px;width:34px">Search</div>
    <div class="disabled">Send Request</div>
    <div class="person" style="top:168px"><span class="box"></span><span class="avatar av1" role="img" aria-label="Colleague photo"></span><div class="who">Mei Lin Tan<small>Application Design Capabilities</small></div><span class="add">Add</span></div>
    <div class="person" style="top:201px"><span class="box"></span><span class="avatar av2" role="img" aria-label="Colleague photo"></span><div class="who">Harold Dunmore<small>UI/UX Designer</small></div><span class="add">Add</span></div>
    <div class="person" style="top:235px"><span class="box on"><svg viewBox="0 0 5 5" fill="none" stroke="#fff" stroke-width=".8"><path d="M1 2.6l1 1 2-2.2"/></svg></span><span class="avatar av3" role="img" aria-label="Colleague photo"></span><div class="who">Mark Tolliver<small>Front-end Developer</small></div><span class="add">Add</span></div>
    <div class="person" style="top:268px"><span class="box"></span><span class="avatar av4" role="img" aria-label="Colleague photo"></span><div class="who">Alina Kessler<small>Cybersecurity Analyst</small></div><span class="add">Add</span></div>
    <div class="person" style="top:302px"><span class="box on"><svg viewBox="0 0 5 5" fill="none" stroke="#fff" stroke-width=".8"><path d="M1 2.6l1 1 2-2.2"/></svg></span><span class="avatar av5" role="img" aria-label="Colleague photo"></span><div class="who">Rupert Calder<small>DevOps Engineer</small></div><span class="add">Add</span></div>
    <div class="pager edge" style="left:423px;width:32px">‹ Back</div><div class="pager cur" style="left:463px">1</div>
    <div class="pager" style="left:488px;top:346px">2</div><div class="pager" style="left:506px;top:346px">3</div><div class="pager" style="left:524px;top:346px">4</div><div class="pager" style="left:543px;top:346px">5</div>
    <div class="pager edge" style="left:567px;width:28px">Next ›</div>
    <div class="pct">65<small>%</small></div><div class="track"><i style="width:402px"></i></div>
    <div class="btn-line goback">Go Back</div><div class="skip">Skip ›</div><div class="btn-fill next">Next</div>
    <div class="overlay"></div>
    <div class="modal">
      <h3>Endorsements</h3>
      <div class="pair"><span class="av3" role="img" aria-label="Colleague photo"></span><span class="av5" role="img" aria-label="Colleague photo"></span></div>
      <p>You will add <b>2</b> colleagues to endorsement you.</p>
      <label>Effective Date</label>
      <div class="sel">Select date<svg viewBox="0 0 8 8" fill="none" stroke="#4a5562" stroke-width="1"><path d="M2 3l2 2 2-2"/></svg></div>
      <div class="btn-line" style="left:15px;top:118px;width:35px">Cancel</div>
      <div class="btn-fill" style="left:118px;top:118px;width:35px">Submit</div>
    </div>
  </section>

  <!-- 9: Submission -->
  <section class="screen" style="left:885px;top:1825px">
    <div class="nav"><div class="brand"><i></i>Skillmark</div><div class="nav-links"><span class="on">Assessments</span><span>Colleagues</span><span>Results</span></div><div class="nav-icons"><svg viewBox="0 0 16 16" fill="none" stroke="#fff" stroke-width="1.4"><path d="M4 11V7a4 4 0 0 1 8 0v4l1 1H3z"/><path d="M7 14h2"/></svg><svg viewBox="0 0 16 16" fill="none" stroke="#fff" stroke-width="1.4"><circle cx="8" cy="8" r="2.3"/><circle cx="8" cy="8" r="5.5" stroke-dasharray="2.2 1.4"/></svg><span class="me" role="img" aria-label="User profile photo"></span></div></div>
    <div class="crumb"><svg viewBox="0 0 12 12" fill="none" stroke="#0e78bb" stroke-width="1"><circle cx="6" cy="6" r="5"/><path d="M8.5 6h-5M5.5 4L3.5 6l2 2"/></svg><span class="link">Assessment</span>/<span>Application Design Capabilities</span></div>
    <div class="page-title"><svg viewBox="0 0 12 12" fill="none" stroke="#1f2a37" stroke-width="1"><rect x="1.5" y="1" width="8" height="10" rx=".8"/><path d="M3.5 4h4M3.5 6h2.5"/><circle cx="8" cy="8.5" r="1.8"/></svg><h2>Application Design Capabilities</h2></div>
    <div class="updated">Last Updated: 23/05/2024</div>
    <div class="meta-band"><span class="m" style="left:47px">Assessment Date: <b>May 20, 2024</b></span><span class="m" style="left:154px">Assessment Type: <b>UI/UX Skill</b></span><span class="m" style="left:253px">Due Date: 24/05/2024</span><div class="chips"><span class="chip">Quiz</span><span class="chip">Endorsement</span><span class="chip">Submission</span></div></div>
    <div class="step done" style="top:117px">Quiz<svg class="ok" viewBox="0 0 8 8"><circle cx="4" cy="4" r="4" fill="#10939b"/><path d="M2.3 4.1l1.2 1.2 2.3-2.5" stroke="#fff" fill="none" stroke-width=".9"/></svg></div><div class="step done" style="top:145px">Endorsement<svg class="ok" viewBox="0 0 8 8"><circle cx="4" cy="4" r="4" fill="#10939b"/><path d="M2.3 4.1l1.2 1.2 2.3-2.5" stroke="#fff" fill="none" stroke-width=".9"/></svg></div><div class="step active" style="top:172px">Submission</div>
    <div class="sect">Submission</div><div class="btn-line save">Save Progress</div>
    <div class="lbl" style="left:196px;top:148px">Document Name</div>
    <div class="input" style="left:196px;top:156px;width:120px">MyPortfolio_2</div>
    <div class="lbl" style="left:327px;top:148px">Document Category</div>
    <div class="input" style="left:327px;top:156px;width:120px">Resume<svg viewBox="0 0 8 8" fill="none" stroke="#4a5562" stroke-width="1"><path d="M2 3l2 2 2-2"/></svg></div>
    <div class="lbl" style="left:196px;top:182px">Note</div>
    <div class="textarea">Write here</div>
    <div class="drop"><span class="up"><svg viewBox="0 0 10 10" fill="none" stroke="#0e78bb" stroke-width="1"><path d="M1 6v3h8V6M5 7V1M3 3l2-2 2 2"/></svg></span>Drag &amp; Drop here for upload<br>or <b>browse</b> file</div>
    <div class="note" style="top:152px;height:70px"><h4>Note</h4>Lorem ipsum dolor sit amet, consecteteur adispiscing elit. Lorem ipsum dolor sit amet, consecteteur adispiscing.</div>
    <div class="pct">75<small>%</small></div><div class="track"><i style="width:502px"></i></div>
    <div class="btn-line goback">Go Back</div><div class="btn-fill" style="left:525px;top:387px;width:70px">Submit Assessment</div>
  </section>

</div>
</body>
</html>
```